New website design and logo for FlintBoro.com to help ignite the website sales.

Hi designers,

Flintboro is a new welding brand that is selling welding equipement.

Currently I have around 5 to 10 products. The issue is that the site itself does not do that much of sales. So I have to do something about the seo etc. but that is out of scope for the design.

What is in scope is to comeup with a new logo and website look and feel that is in line with the customers.

men, non professionals, garage, home improvements, perhaps sme ( small mediul entreprice business that want to start in the welding industry.

Products are midrange prices and quality. The look and feel must breath cool stuff, sexy ( women in working cloths carrying welding gloves, other protection gear and weldels)

The wedsite is build in wordpress with the Kora theme. I am an IT guy myself withhout any creativity in me :( so if you can help me with that that would be great.

Please have a quick look at flintboro.com

Best regards,
Joris

Target Market(s)

non professional welders that do metal work in there garage

Coding

Coded - Design and coding required

Number of Pages Required

3 page

Font styles to use
Sans Serif

Colors
0355a3
ffc214

Requirements
Must have
• I would like to see a new homepage and product page design together with a new logo.
Nice to have
• shop design

```html
<!DOCTYPE html>
<html lang="en">
<head>
<meta charset="utf-8">
<title>Flintboro – Welding Equipment</title>
<link rel="stylesheet" href="https://fonts.googleapis.com/css2?family=Roboto:wght@400;500;700&family=Ubuntu:wght@500;700&display=swap">
<style>
:root{
  --blue:#0a6cd6;
  --blue-dark:#0355a3;
  --yellow:#ffc214;
  --ink:#1b1b1b;
  --footer:#232323;
  --white:#ffffff;
  --muted:#d8d8d8;
  --card-shadow:0 2px 8px rgba(0,0,0,.12);
}
*{box-sizing:border-box;margin:0;padding:0}
html,body{width:1200px;height:2229px;overflow:hidden}
body{font-family:'Roboto',sans-serif;color:var(--ink);background:var(--white);position:relative}
.topline{position:absolute;left:0;top:0;width:1200px;height:4px;background:var(--yellow);z-index:3}

.header{position:absolute;left:0;top:0;width:1200px;height:84px;background:var(--white);z-index:2}
.brand-badge{position:absolute;left:85px;top:-10px;width:142px;height:146px;border-radius:0 0 71px 71px;background:var(--white);z-index:4;display:flex;align-items:center;justify-content:center;flex-direction:column}
.brand-badge .dot{width:16px;height:16px;border-radius:50%;background:var(--yellow);margin-bottom:6px}
.brand-badge .name{font-family:'Ubuntu',sans-serif;font-weight:700;font-size:20px;color:var(--blue-dark)}
.nav{position:absolute;top:34px;left:0;font-size:14.5px;font-weight:500;letter-spacing:.2px}
.nav a{position:absolute;white-space:nowrap;color:var(--ink);text-decoration:none}
.nav a.active{color:var(--blue)}
.nav .caret{display:inline-block;margin-left:6px;vertical-align:2px}
.user-tools{position:absolute;top:34px;left:916px;font-size:14.5px;font-weight:500;display:flex;align-items:center;gap:8px;white-space:nowrap}
.user-tools .sep{margin:0 8px}

.hero{position:absolute;left:0;top:84px;width:1200px;height:599px;background:radial-gradient(ellipse at 62% 60%,#b26a24 0%,#4b3420 25%,#1d2634 55%,#0e1520 100%)}
.hero-title{position:absolute;left:0;width:1200px;top:212px;text-align:center;font-family:'Ubuntu',sans-serif;font-weight:700;font-size:33px;line-height:45px;color:var(--white)}
.btn-hero{position:absolute;left:527px;top:331px;width:145px;height:49px;border-radius:25px;background:var(--blue);color:var(--white);font-family:'Ubuntu',sans-serif;font-weight:700;font-size:16px;display:flex;align-items:center;justify-content:center}
.hero-arrow{position:absolute;top:284px}
.scroll-hint{position:absolute;left:565px;top:648px;width:70px;height:70px;border-radius:50%;background:var(--white);border:1px solid #e3e3e3;z-index:2;display:flex;align-items:center;justify-content:center}

.section-title{position:absolute;left:0;width:1200px;top:782px;text-align:center;font-family:'Ubuntu',sans-serif;font-weight:700;font-size:33px}
.section-rule{position:absolute;left:531px;top:833px;width:138px;height:3px;background:var(--yellow)}

.card{position:absolute;width:301px;height:394px;background:var(--white);box-shadow:var(--card-shadow);text-align:center}
.card.featured{border:3px solid var(--yellow)}
.card .shot{position:absolute;left:60px;top:20px;width:181px;height:190px;border-radius:6px}
.card .title{position:absolute;left:0;width:100%;top:236px;font-size:20px;font-weight:500}
.card .stars{position:absolute;left:0;width:100%;top:267px;color:var(--yellow);font-size:11px;letter-spacing:2px}
.card .price{position:absolute;left:0;width:100%;top:289px;font-size:17px;font-weight:500}
.card .actions{position:absolute;left:60px;top:326px;display:flex;gap:9px;align-items:center}
.btn-outline{width:128px;height:43px;border:2px solid var(--blue-dark);border-radius:22px;font-size:15px;font-weight:500;letter-spacing:.3px;display:flex;align-items:center;justify-content:center}
.btn-cart{width:45px;height:45px;border-radius:50%;background:var(--blue);display:flex;align-items:center;justify-content:center}

.btn-all{position:absolute;left:496px;top:1764px;width:209px;height:49px;border-radius:25px;background:var(--yellow);color:var(--white);font-family:'Ubuntu',sans-serif;font-weight:700;font-size:16px;display:flex;align-items:center;justify-content:center}

.footer{position:absolute;left:0;top:1905px;width:1200px;height:324px;background:var(--footer);color:var(--white)}
.footer-brand{position:absolute;left:112px;top:58px;display:flex;align-items:center;gap:10px;font-family:'Ubuntu',sans-serif;font-weight:700;font-size:24px;color:var(--yellow)}
.footer-brand .dot{width:18px;height:18px;border-radius:50%;background:var(--yellow)}
.footer-col{position:absolute;top:50px}
.footer-col h4{font-size:18px;font-weight:500;margin-bottom:20px}
.footer-col li{list-style:none;font-size:14px;line-height:24px;color:var(--muted);padding-left:2px}
.newsletter{position:absolute;left:811px;top:98px;width:277px;height:43px;border:1.5px solid var(--white);border-radius:22px;font-size:12.5px;padding-left:21px;display:flex;align-items:center}
.newsletter .send{position:absolute;right:-2px;top:-2px;width:44px;height:44px;border-radius:50%;background:var(--white);display:flex;align-items:center;justify-content:center}
.contact-line{position:absolute;left:811px;top:166px;font-size:14px;display:flex;align-items:center;gap:20px;color:var(--muted)}
.footer-rule{position:absolute;left:112px;top:262px;width:976px;height:1px;background:#6a6a6a}
.copyright{position:absolute;left:112px;top:277px;font-size:12.5px;color:var(--muted)}
.social{position:absolute;left:881px;top:269px;display:flex;gap:8px}
.social span{width:35px;height:35px;border-radius:50%;border:1.5px solid var(--yellow)}
</style>
</head>
<body>
<div class="topline"></div>

<header class="header">
  <nav class="nav">
    <a class="active" style="left:352px">HOME</a>
    <a style="left:419px">OUR PRODUCTS<svg class="caret" width="9" height="6" viewBox="0 0 9 6"><path d="M1 1l3.5 3.5L8 1" fill="none" stroke="#1b1b1b" stroke-width="1.5"/></svg></a>
    <a style="left:573px">SHOPPING CART</a>
    <a style="left:716px">CONTACT US</a>
  </nav>
  <div class="user-tools">
    <svg width="16" height="16" viewBox="0 0 16 16"><circle cx="8" cy="8" r="7" fill="none" stroke="#0a6cd6" stroke-width="1.5"/><circle cx="8" cy="6.5" r="2.5" fill="#0a6cd6"/><path d="M3.5 12.5c1.5-2.5 7.5-2.5 9 0" fill="#0a6cd6"/></svg>
    <span>LOGIN</span><span class="sep">|</span>
    <svg width="16" height="14" viewBox="0 0 16 14"><path d="M0 1h3l2 8h8l2-6H4" fill="none" stroke="#1b1b1b" stroke-width="1.8"/><circle cx="6" cy="12" r="1.4"/><circle cx="12" cy="12" r="1.4"/></svg><span style="margin-left:-6px">(0)</span>
    <svg style="margin-left:14px" width="14" height="14" viewBox="0 0 14 14"><circle cx="6" cy="6" r="4.5" fill="none" stroke="#1b1b1b" stroke-width="2"/><path d="M9.5 9.5L13 13" stroke="#1b1b1b" stroke-width="2.2"/></svg>
  </div>
</header>
<div class="brand-badge"><span class="dot"></span><span class="name">Flintboro</span></div>

<section class="hero" role="img" aria-label="Photo of a welder in a protective helmet with bright sparks flying">
  <svg class="hero-arrow" style="left:42px" width="20" height="32" viewBox="0 0 20 32"><path d="M16 3L4 16l12 13" fill="none" stroke="#fff" stroke-width="3"/></svg>
  <svg class="hero-arrow" style="left:1139px" width="20" height="32" viewBox="0 0 20 32"><path d="M4 3l12 13L4 29" fill="none" stroke="#fff" stroke-width="3"/></svg>
  <h1 class="hero-title">Simple welding of steel and aluminum Get<br>great results with tools that work</h1>
  <div class="btn-hero">SHOP NOW</div>
</section>
<div class="scroll-hint">
  <svg width="18" height="18" viewBox="0 0 18 18"><path d="M3 3l6 6 6-6M3 9l6 6 6-6" fill="none" stroke="#ffc214" stroke-width="2"/></svg>
</div>

<h2 class="section-title">Our Products</h2>
<div class="section-rule"></div>

<div class="card" style="left:112px;top:883px">
  <div class="shot" role="img" aria-label="Red MIG welding machine" style="background:linear-gradient(160deg,#d9463a,#3b2b2b)"></div>
  <div class="title">MIG-250P</div><div class="stars">★★★★★</div><div class="price">€ 795.00</div>
  <div class="actions"><div class="btn-outline">SHOP NOW</div><div class="btn-cart"><svg width="20" height="18" viewBox="0 0 16 14"><path d="M0 1h3l2 8h8l2-6H4" fill="none" stroke="#fff" stroke-width="1.8"/><circle cx="6" cy="12" r="1.4" fill="#fff"/><circle cx="12" cy="12" r="1.4" fill="#fff"/></svg></div></div>
</div>
<div class="card featured" style="left:449px;top:883px">
  <div class="shot" role="img" aria-label="Blue and grey MIG welding machine" style="left:57px;top:17px;background:linear-gradient(90deg,#b8bcc4,#3f78c9)"></div>
  <div class="title" style="top:233px">MIG-2500</div><div class="stars" style="top:264px">★★★★★</div><div class="price" style="top:286px">€745,00</div>
  <div class="actions" style="left:57px;top:323px"><div class="btn-outline">SHOP NOW</div><div class="btn-cart"><svg width="20" height="18" viewBox="0 0 16 14"><path d="M0 1h3l2 8h8l2-6H4" fill="none" stroke="#fff" stroke-width="1.8"/><circle cx="6" cy="12" r="1.4" fill="#fff"/><circle cx="12" cy="12" r="1.4" fill="#fff"/></svg></div></div>
</div>
<div class="card" style="left:786px;top:883px">
  <div class="shot" role="img" aria-label="Black auto-darkening welding helmet with wide view" style="background:radial-gradient(circle at 45% 40%,#7a5aa8,#2a2a2a 60%,#e9e9e9 100%)"></div>
  <div class="title">Welding helmet 180 degrees</div><div class="stars">★★★★★</div><div class="price">€109,00</div>
  <div class="actions"><div class="btn-outline">SHOP NOW</div><div class="btn-cart"><svg width="20" height="18" viewBox="0 0 16 14"><path d="M0 1h3l2 8h8l2-6H4" fill="none" stroke="#fff" stroke-width="1.8"/><circle cx="6" cy="12" r="1.4" fill="#fff"/><circle cx="12" cy="12" r="1.4" fill="#fff"/></svg></div></div>
</div>

<div class="card" style="left:112px;top:1314px">
  <div class="shot" role="img" aria-label="Black welding helmet with large view window" style="background:radial-gradient(circle at 40% 40%,#8a5ac8,#222 55%,#f0f0f0 100%)"></div>
  <div class="title">Welding helmet large view</div><div class="stars">★★★★★</div><div class="price">€89,00</div>
  <div class="actions"><div class="btn-outline">SHOP NOW</div><div class="btn-cart"><svg width="20" height="18" viewBox="0 0 16 14"><path d="M0 1h3l2 8h8l2-6H4" fill="none" stroke="#fff" stroke-width="1.8"/><circle cx="6" cy="12" r="1.4" fill="#fff"/><circle cx="12" cy="12" r="1.4" fill="#fff"/></svg></div></div>
</div>
<div class="card" style="left:449px;top:1314px">
  <div class="shot" role="img" aria-label="Blue and yellow leather welding gloves" style="background:linear-gradient(135deg,#2536b8,#e8b93a)"></div>
  <div class="title">Welding gloves Blue</div><div class="stars">★★★★★</div><div class="price">€22,40</div>
  <div class="actions"><div class="btn-outline">SHOP NOW</div><div class="btn-cart"><svg width="20" height="18" viewBox="0 0 16 14"><path d="M0 1h3l2 8h8l2-6H4" fill="none" stroke="#fff" stroke-width="1.8"/><circle cx="6" cy="12" r="1.4" fill="#fff"/><circle cx="12" cy="12" r="1.4" fill="#fff"/></svg></div></div>
</div>
<div class="card" style="left:786px;top:1314px">
  <div class="shot" role="img" aria-label="Black leather welding gloves" style="background:linear-gradient(160deg,#3c3c36,#1c1c1a)"></div>
  <div class="title">Welding gloves Black</div><div class="stars">★★★★★</div><div class="price">€22,40</div>
  <div class="actions"><div class="btn-outline">SHOP NOW</div><div class="btn-cart"><svg width="20" height="18" viewBox="0 0 16 14"><path d="M0 1h3l2 8h8l2-6H4" fill="none" stroke="#fff" stroke-width="1.8"/><circle cx="6" cy="12" r="1.4" fill="#fff"/><circle cx="12" cy="12" r="1.4" fill="#fff"/></svg></div></div>
</div>

<div class="btn-all">VIEW ALL PRODUCTS</div>

<footer class="footer">
  <div class="footer-brand"><span class="dot"></span>Flintboro</div>
  <div class="footer-col" style="left:356px"><h4>Useful Links</h4><ul><li>Home</li><li>Our Products</li><li>Shopping Cart</li><li>Latest Blog</li><li>Contact Us</li></ul></div>
  <div class="footer-col" style="left:584px"><h4>About Links</h4><ul><li>Site Map</li><li>FAQ</li><li>Privacy Policy</li><li>Terms Of Use</li></ul></div>
  <div class="footer-col" style="left:810px"><h4>Newsletter</h4></div>
  <div class="newsletter">Email Address
    <span class="send"><svg width="20" height="20" viewBox="0 0 20 20"><path d="M2 10L18 2l-4 16-4-6z" fill="#0a6cd6"/></svg></span>
  </div>
  <div class="contact-line"><svg width="13" height="13" viewBox="0 0 14 14"><path d="M3 1l3 3-1.5 2c1 2 2 3 3.5 3.5L10 8l3 3-2 2C6 13 1 8 1 3z" fill="#0a6cd6"/></svg>+31(0)612 345 678</div>
  <div class="footer-rule"></div>
  <div class="copyright">© Copyrights 2021 Company Name. All Rights Reserved</div>
  <div class="social"><span></span><span></span><span></span><span></span><span></span></div>
</footer>
</body>
</html>
```